Consulting Company PowerPoint Template Design

We are looking for an updated PowerPoint template design or our 55 person energy consulting firm (K7) based in San Francisco (www.kseven-example.com). We would like two versions of the same PowerPoint template in a 16:9 and 4:3 format with our existing logo.

We have an existing color scheme and template and are seeking your help to polish/update the template design for wide format and create a flexible template that is easy to use with content from Excel and Word. Our current template, and a couple of examples that we like are attached.

Specific requests include:

• Dark background for slide title
• A narrow section header
• Maximizing white space for content
• A limited number of well designed Master template layouts to choose from
• A selection of title and section header slides that are not San Francisco specific with some variety to chose from ideally with a focus on energy or nature, graphics/visuals.

For examples of energy specific templates see:
https://www.brightslidehub.example/energy/powerpoint-templates/0.html

Requirements
Must have
• Must use our logo but open to other designs, fonts, and styles for the PowerPoint template.
• Please use our existing color scheme found in the attached Excel file.
• Also we would like the ability to easily copy and paste from our existing/original template to the new template. In other words we would like backward compatibility to apply the new template format to our old PowerPoints that use our existing template.

```html
<!DOCTYPE html>
<html lang="en">
<head>
<meta charset="utf-8">
<title>K7 Slide Template – Bullet Layouts</title>
<link rel="stylesheet" href="https://fonts.googleapis.com/css2?family=Titillium+Web:wght@400;600;700&display=swap">
<style>
  :root {
    --navy: #05526f;
    --gold: #d6b26c;
    --ink: #1e1e1e;
    --paper: #ffffff;
    --backdrop: #000000;
  }
  * { box-sizing: border-box; margin: 0; padding: 0; }
  html, body {
    width: 790px; height: 1200px; overflow: hidden;
    background: var(--backdrop);
    font-family: "Titillium Web", sans-serif;
  }
  .slide {
    position: absolute; left: 30px; width: 721px; height: 541px;
    background: var(--paper); overflow: hidden;
  }
  .slide--dot { top: 27px; }
  .slide--badge { top: 613px; }

  .title-bar {
    position: absolute; left: 0; top: 0; width: 100%; height: 39px;
    background: var(--navy);
  }
  .title-rule { position: absolute; left: 0; top: 39px; }
  .slide-title {
    position: absolute; left: 11px; top: 5px;
    font-size: 20px; font-weight: 600; color: var(--paper); letter-spacing: 0.2px;
  }
  .slide-title .accent { color: var(--gold); }
  .brand-mark {
    position: absolute; right: 7px; top: 6px; width: 48px; height: 48px;
    border-radius: 50%; background: var(--navy);
    border: 3px solid var(--paper); box-shadow: 0 0 0 1px #c9d6dc;
    display: flex; align-items: center; justify-content: center;
    font-size: 17px; font-weight: 700; color: var(--paper);
  }

  .point { position: absolute; left: 0; width: 100%; }
  .point-marker {
    position: absolute; left: 27px; top: 5px; width: 13px; height: 13px;
    border-radius: 50%; background: var(--navy);
  }
  .slide--badge .point-marker {
    left: 15px; top: -1px; width: 26px; height: 26px;
    border: 2px solid var(--paper); box-shadow: 0 0 0 1px #c9d6dc;
    display: flex; align-items: center; justify-content: center;
    font-size: 9px; font-weight: 700; color: var(--paper);
  }
  .point-title {
    position: absolute; left: 49px; top: -3px;
    font-size: 17px; font-weight: 700; color: var(--navy); white-space: nowrap;
  }
  .point-body {
    position: absolute; left: 49px; top: 21px; width: 630px;
    font-size: 13.4px; line-height: 20px; color: var(--ink);
  }

  .footer-bar {
    position: absolute; left: 0; bottom: 0; width: 100%; height: 27px;
    background: var(--navy);
  }
  .footer-name {
    position: absolute; left: 5px; top: 2px;
    font-size: 15.5px; font-weight: 700; color: var(--paper);
  }
  .page-tab { position: absolute; right: 0; bottom: 0; }
  .page-number {
    position: absolute; right: 21px; bottom: 5px;
    font-size: 12px; color: var(--paper); letter-spacing: 0.5px;
  }
</style>
</head>
<body>

<section class="slide slide--dot">
  <div class="title-bar"><h1 class="slide-title"><span class="accent">PROJECT</span> TITLE HERE</h1></div>
  <svg class="title-rule" width="721" height="6"><polygon points="0,0 700,0 693,5 0,5" fill="var(--gold)"/></svg>
  <div class="brand-mark">K7</div>

  <div class="point" style="top:103px"><span class="point-marker"></span><h2 class="point-title">Subtext Title Here</h2>
    <p class="point-body">Rising Path contributes to the eradication of extreme poverty by partnering with governments and global agencies to ensure that, through policy</p></div>
  <div class="point" style="top:185px"><span class="point-marker"></span><h2 class="point-title">Subtext Title Here</h2>
    <p class="point-body">Rising Path contributes to the eradication of extreme poverty by partnering with governments and global agencies to ensure that, through policy</p></div>
  <div class="point" style="top:276px"><span class="point-marker"></span><h2 class="point-title">Subtext Title Here</h2>
    <p class="point-body">Rising Path contributes to the eradication of extreme poverty by partnering with governments and global agencies to ensure that, through policy</p></div>
  <div class="point" style="top:367px"><span class="point-marker"></span><h2 class="point-title">Subtext Title Here</h2>
    <p class="point-body">Rising Path contributes to the eradication of extreme poverty by partnering with governments and global agencies to ensure that, through policy</p></div>

  <div class="footer-bar"><span class="footer-name">Kinetic Seven Economics</span></div>
  <svg class="page-tab" width="66" height="27"><polygon points="6,0 66,0 66,27 12,27 3,10" fill="var(--gold)" stroke="var(--paper)" stroke-width="2"/></svg>
  <span class="page-number">01</span>
</section>

<section class="slide slide--badge">
  <div class="title-bar"><h1 class="slide-title"><span class="accent">PROJECT</span> TITLE HERE</h1></div>
  <svg class="title-rule" width="721" height="6"><polygon points="0,0 700,0 693,5 0,5" fill="var(--gold)"/></svg>
  <div class="brand-mark">K7</div>

  <div class="point" style="top:103px"><span class="point-marker">K7</span><h2 class="point-title">Subtext Title Here</h2>
    <p class="point-body">Rising Path contributes to the eradication of extreme poverty by partnering with governments and global agencies to ensure that, through policy</p></div>
  <div class="point" style="top:185px"><span class="point-marker">K7</span><h2 class="point-title">Subtext Title Here</h2>
    <p class="point-body">Rising Path contributes to the eradication of extreme poverty by partnering with governments and global agencies to ensure that, through policy</p></div>
  <div class="point" style="top:276px"><span class="point-marker">K7</span><h2 class="point-title">Subtext Title Here</h2>
    <p class="point-body">Rising Path contributes to the eradication of extreme poverty by partnering with governments and global agencies to ensure that, through policy</p></div>
  <div class="point" style="top:367px"><span class="point-marker">K7</span><h2 class="point-title">Subtext Title Here</h2>
    <p class="point-body">Rising Path contributes to the eradication of extreme poverty by partnering with governments and global agencies to ensure that, through policy</p></div>

  <div class="footer-bar"><span class="footer-name">Kinetic Seven Economics</span></div>
  <svg class="page-tab" width="66" height="27"><polygon points="6,0 66,0 66,27 12,27 3,10" fill="var(--gold)" stroke="var(--paper)" stroke-width="2"/></svg>
  <span class="page-number">01</span>
</section>

</body>
</html>
```